Business Card Design Project

We need a Business Card for an Mechanical Engineering firm in Singapore. The design should be Modern & Technical looking, yet eye catching.

Our company deals in Cutting Tools & Machine Accessories for the Manufacturing Industries such as Oil & Gas, Aero Space, etc... For more information on our Company, you can either email me or view our website www.torvalen.com.sg.

We are trying to revamp our image to give our consumers a fresh new perspective to our company, so we welcome all ideas.

Industry/Entity Type

Business

Requirements
Must have
• Must incorporate New Company Logo into the card as shown in Uploaded file.

```html
<!DOCTYPE html>
<html lang="en">
<head>
<meta charset="utf-8">
<title>Torvalen Tools – Business Card</title>
<link rel="stylesheet" href="https://fonts.googleapis.com/css2?family=Ubuntu:wght@400;500&display=swap">
<style>
  :root {
    --brand-red: #8f1b37;
    --label-pink: #e4a9b7;
    --ink: #4a1020;
    --card: #ffffff;
    --backdrop: #dfe3e3;
    --stripe: 7px;
  }
  * { margin: 0; padding: 0; box-sizing: border-box; }
  html, body {
    width: 1200px; height: 900px; overflow: hidden;
    background: var(--backdrop);
    font-family: "Ubuntu", Arial, sans-serif;
  }
  .card {
    position: absolute; left: 80px; top: 150px;
    width: 1040px; height: 600px;
    background: var(--card);
    box-shadow: 0 10px 30px rgba(0,0,0,0.18);
    overflow: hidden;
  }
  .holder-name {
    position: absolute; left: 106px; top: 82px;
    font-size: 44px; font-weight: 400; color: var(--ink);
  }
  .name-rule {
    position: absolute; left: 0; top: 145px;
    width: 726px; height: 7px; background: var(--brand-red);
  }
  .holder-title {
    position: absolute; left: 106px; top: 166px;
    font-size: 31px; color: var(--ink);
  }
  .info-band {
    position: absolute; left: 0; width: 524px;
    background: var(--brand-red); color: #fff;
    padding-left: 64px;
  }
  .info-band::before, .info-band::after {
    content: ""; position: absolute; top: 0; bottom: 0; width: 36px;
    background: repeating-linear-gradient(to bottom,
      #fff 0, #fff var(--stripe),
      var(--brand-red) var(--stripe), var(--brand-red) calc(var(--stripe) * 2));
  }
  .info-band::before { left: 0; }
  .info-band::after { right: 0; }
  .contact-band {
    top: 282px; height: 96px;
    display: flex; flex-direction: column; justify-content: center; gap: 6px;
    font-size: 27px;
  }
  .contact-row { display: flex; }
  .contact-label { width: 106px; color: var(--label-pink); }
  .address-band {
    top: 396px; height: 186px;
    padding-top: 14px; font-size: 27px; line-height: 38px;
  }
  .company-name { font-weight: 500; margin-bottom: 8px; color: #f6dde3; }
  .brand {
    position: absolute; left: 568px; top: 380px; width: 424px;
    display: flex; align-items: center; justify-content: center; gap: 16px;
    color: var(--brand-red); font-size: 48px; font-weight: 500;
    letter-spacing: 1px;
  }
  .brand-dot {
    width: 28px; height: 28px; border-radius: 50%; background: var(--brand-red);
    flex: none;
  }
  .web-bar {
    position: absolute; left: 568px; top: 504px;
    width: 424px; height: 57px; background: var(--brand-red);
    color: #fff; font-size: 28px; font-weight: 500;
    display: flex; align-items: center; justify-content: center;
    letter-spacing: 1px;
  }
</style>
</head>
<body>
  <main class="card">
    <h1 class="holder-name">Marcus Tan</h1>
    <div class="name-rule"></div>
    <p class="holder-title">President-CEO</p>

    <section class="info-band contact-band">
      <div class="contact-row"><span class="contact-label">mobile</span><span>65-61234570</span></div>
      <div class="contact-row"><span class="contact-label">email</span><span>hello@torvalen.com.sg</span></div>
    </section>

    <section class="info-band address-band">
      <p class="company-name">Torvalen Tools Pte Ltd</p>
      <p>27 Kallang Way #03-08</p>
      <p>Kallang Trade Centre</p>
      <p>Singapore 349581</p>
    </section>

    <div class="brand"><span class="brand-dot"></span><span>TORVALEN TOOLS</span></div>
    <div class="web-bar">www.torvalen.com.sg</div>
  </main>
</body>
</html>
```